Etiketten für Olivenöl-Intensivcreme
Zielgruppe
Wir produzieren Bio-Food, u.a. Wein und Olivenöl. Jetzt soll eine Olivenöl-Intensivcreme im Bereich Kosmetik auf dem Markt platziert werden. Unsere Zielgruppe hat ein sehr breites Altersspektrum (jung bis alt), ist naturverbunden, tierlieb, gebildet, kritisch-reflektierend, weiß gute Qualität zu schätzen, ist überwiegend weiblich. Die Olivenöl-Intensivcreme hat eine sehr breite Verwendung und soll sich als 'Allzweckwaffe' in jedem Haushalt etablieren (Babyhaut-Pflege, Lippenpflege, Ganzkörperpflege, Hand-Schutzcreme etc.).
Aufgabenstellung
Die Creme soll heißen: Velamira (es könnte z.B. der Buchstabe 'O' durch eine Olive ersetzt werden). Es gibt zwei Etikette (Deckeloberseite der Metalldose und auf dem Boden). Der Durchmesser der Etikette ist jeweils 5,5 cm. Die Deckelunterseite gilt reinen Pflichtangaben. Im Dateidownloadbereich sind die Textvorgaben für die Etikette. MUT zur Farbe! Wir sind NICHT brav und angepasst! Orange kann Akzente setzen bzw. für Aufmerksamkeit im Regal sorgen.

```html
<!DOCTYPE html>
<html lang="de">
<head>
<meta charset="utf-8">
<title>Velamira – Deckeletikett</title>
<link rel="stylesheet" href="https://fonts.googleapis.com/css2?family=Rubik:wght@400&family=Varela+Round&display=swap">
<style>
  :root {
    --bg: #f4f4f4;
    --label: #ffffff;
    --rim-outer: #c9c9c9;
    --rim-inner: #e6e6e6;
    --ink: #1d1d1d;
    --accent: #ef8152;
    --accent-soft: #f7b899;
    --badge: #1b1b1b;
    --badge-text: #ffffff;
  }
  html, body {
    margin: 0;
    padding: 0;
    width: 1200px;
    height: 1160px;
    overflow: hidden;
    background: var(--bg);
  }
  .label-art {
    display: block;
    width: 1200px;
    height: 1160px;
  }
  .brand-name {
    font-family: "Rubik", sans-serif;
    font-weight: 400;
    font-size: 56px;
    fill: var(--ink);
    letter-spacing: 1px;
  }
  .badge-text {
    font-family: "Rubik", sans-serif;
    font-size: 38px;
    fill: var(--badge-text);
  }
  .product-name {
    font-family: "Varela Round", sans-serif;
    font-size: 200px;
    fill: var(--accent);
  }
  .product-type {
    font-family: "Rubik", sans-serif;
    font-size: 54px;
    fill: var(--ink);
  }
  .product-claims {
    font-family: "Rubik", sans-serif;
    font-size: 44px;
    fill: var(--ink);
  }
</style>
</head>
<body>
<svg class="label-art" viewBox="0 0 1200 1160" xmlns="http://www.w3.org/2000/svg">
  <defs>
    <linearGradient id="branchTone" x1="0" y1="1" x2="1" y2="0">
      <stop offset="0" stop-color="var(--accent)"/>
      <stop offset="1" stop-color="var(--accent-soft)"/>
    </linearGradient>
  </defs>

  <!-- Etikett mit Rand -->
  <g class="lid-label">
    <circle class="rim" cx="600" cy="580" r="500" fill="var(--rim-outer)"/>
    <circle class="rim-highlight" cx="600" cy="580" r="486" fill="var(--rim-inner)"/>
    <circle class="label-face" cx="600" cy="580" r="468" fill="var(--label)"/>
  </g>

  <!-- Markenname -->
  <text class="brand-name" x="600" y="322" text-anchor="middle">KORVAN.HOF</text>

  <!-- Badge Naturkosmetik -->
  <g class="badge">
    <circle cx="858" cy="464" r="114" fill="var(--badge)"/>
    <text class="badge-text" x="858" y="450" text-anchor="middle">NATUR-</text>
    <text class="badge-text" x="858" y="500" text-anchor="middle">KOSMETIK</text>
  </g>

  <!-- Olivenzweig -->
  <rect class="branch-motif" role="img" aria-label="Olivenzweig mit Blättern über dem Produktnamen"
        x="192" y="398" width="228" height="138" rx="60" fill="url(#branchTone)"/>

  <!-- Produktname -->
  <text class="product-name" x="602" y="716" text-anchor="middle" textLength="760" lengthAdjust="spacingAndGlyphs">VELAMIRA</text>

  <!-- Produktart -->
  <text class="product-type" x="610" y="806" text-anchor="middle">OLIVENÖL-INTENSIVCREME</text>

  <!-- Eigenschaften -->
  <text class="product-claims" x="610" y="924" text-anchor="middle">Bio-Olive . vegan . Pflege-</text>
  <text class="product-claims" x="610" y="988" text-anchor="middle">und Schutzcreme</text>
</svg>
</body>
</html>
```